U.S. Popcorn company needs business cards

We are a popcorn company that manufactures popcorn and sells it to grocery stores worldwide. Our theme is "Americana" and our logo is U.S. route 66 which is the most famous highway in the U.S.

We would like the design to be simple and to use both sides. On the back side we would like to see just the logo and website. The front would be normal details

Target Market(s)

Wholesalers, grocers and distributors

Industry/Entity Type

Manufacture

Contact Information for Business Card

Business name: Prairie Lantern Popcorn
Phone: +1 555 308 4726
Email: Dale@prairielanternpopcorn.com
website: www.prairielanternpopcorn.com
Tag Line: "POPular for a reason"
Name: Dale Whitcombe
Title: Founder/President

Requirements
Must have
• Either this design should be fun or clean and simple. I will let you show me your thougths.
Nice to have
• Anything that ties in the real Hwy Route 66.
• Colors might need to be red, white and blue incorporated.
Should not have
• Not be too busy.

```html
<!DOCTYPE html>
<html lang="en">
<head>
<meta charset="utf-8">
<title>Prairie Lantern Popcorn – Business Cards</title>
<link rel="stylesheet" href="https://fonts.googleapis.com/css2?family=Mulish:ital,wght@0,400;0,700;0,800;1,400&display=swap">
<style>
  :root {
    --stage: #e4e4e4;
    --navy: #112e66;
    --navy-text: #1c3a78;
    --red: #d7232a;
    --white: #ffffff;
    --card-white: #f7f7f7;
    --ink: #2a3d74;
    --faint: #e6e8ee;
  }
  * { box-sizing: border-box; margin: 0; padding: 0; }
  html, body { width: 1200px; height: 576px; overflow: hidden; }
  body {
    background: var(--stage);
    font-family: "Mulish", sans-serif;
    position: relative;
  }
  .card {
    position: absolute;
    top: 139px;
    width: 484px;
    height: 292px;
    border-radius: 6px;
    overflow: hidden;
  }
  .card--back { left: 82px; background: var(--navy); }
  .card--front { left: 602px; background: var(--card-white); }

  /* Back */
  .brand-mark {
    position: absolute;
    left: 0; right: 0;
    top: 62px;
    display: flex;
    flex-direction: column;
    align-items: center;
    gap: 10px;
  }
  .brand-mark__dot {
    width: 22px; height: 22px;
    border-radius: 50%;
    background: var(--red);
  }
  .brand-mark__name {
    color: var(--white);
    font-weight: 800;
    font-size: 30px;
    line-height: 1.1;
    text-align: center;
    letter-spacing: 0.5px;
  }
  .back-web {
    position: absolute;
    left: 0; right: 0;
    top: 256px;
    display: flex;
    align-items: center;
    justify-content: center;
    gap: 12px;
    color: var(--white);
    font-weight: 700;
    font-size: 11.5px;
    letter-spacing: 0.3px;
  }
  .back-web__rule {
    width: 40px; height: 2px;
    background: var(--red);
  }

  /* Front */
  .front-mark {
    position: absolute;
    left: 36px;
    top: 70px;
    width: 160px;
    display: flex;
    flex-direction: column;
    align-items: center;
    gap: 8px;
  }
  .front-mark__dot {
    width: 18px; height: 18px;
    border-radius: 50%;
    background: var(--red);
  }
  .front-mark__name {
    color: var(--navy-text);
    font-weight: 800;
    font-size: 24px;
    line-height: 1.1;
    text-align: center;
  }
  .person {
    position: absolute;
    left: 225px;
    top: 72px;
  }
  .person__name {
    color: var(--red);
    font-weight: 700;
    font-size: 16px;
  }
  .person__title {
    color: var(--ink);
    font-style: italic;
    font-size: 11.5px;
    margin-top: 2px;
  }
  .contacts {
    position: absolute;
    left: 225px;
    top: 132px;
    list-style: none;
  }
  .contacts li {
    display: flex;
    align-items: center;
    gap: 10px;
    color: var(--ink);
    font-size: 13px;
    line-height: 17px;
  }
  .contacts svg { width: 11px; height: 11px; flex: none; }
  .tagline {
    position: absolute;
    left: 0; right: 0;
    top: 244px;
    text-align: center;
    padding-left: 120px;
    color: var(--ink);
    font-size: 15px;
  }
  .tagline__pop { color: var(--red); font-weight: 700; }
  .decor {
    position: absolute;
    background: var(--faint);
    border-radius: 50%;
    opacity: 0.8;
  }
  .decor--top { right: 4px; top: 0; width: 42px; height: 56px; border-radius: 0 0 50% 50%; }
  .decor--bottom { left: 0; bottom: 0; width: 72px; height: 40px; border-radius: 50% 50% 0 0; }
</style>
</head>
<body>

<section class="card card--back" aria-label="Card back">
  <div class="brand-mark">
    <span class="brand-mark__dot"></span>
    <p class="brand-mark__name">Prairie Lantern<br>Popcorn</p>
  </div>
  <div class="back-web">
    <span class="back-web__rule"></span>
    <span>www.prairielanternpopcorn.com</span>
    <span class="back-web__rule"></span>
  </div>
</section>

<section class="card card--front" aria-label="Card front">
  <div class="decor decor--top" role="img" aria-label="Faint popcorn decoration"></div>
  <div class="decor decor--bottom" role="img" aria-label="Faint popcorn decoration"></div>

  <div class="front-mark">
    <span class="front-mark__dot"></span>
    <p class="front-mark__name">Prairie Lantern<br>Popcorn</p>
  </div>

  <div class="person">
    <p class="person__name">Dale Whitcombe</p>
    <p class="person__title">Founder/President</p>
  </div>

  <ul class="contacts">
    <li>
      <svg viewBox="0 0 12 12" aria-hidden="true"><path fill="#d7232a" d="M1 4c0-2 2-3 5-3s5 1 5 3v1H8.5V4h-5v1H1zM3 5.5h6l1.5 5.5h-9z"/><circle cx="6" cy="8" r="1.3" fill="#f7f7f7"/></svg>
      <span>+1 555 308 4726</span>
    </li>
    <li>
      <svg viewBox="0 0 12 12" aria-hidden="true"><rect x="0.5" y="2" width="11" height="8" fill="#d7232a"/><path d="M0.5 2.5 6 7l5.5-4.5" fill="none" stroke="#f7f7f7" stroke-width="1"/></svg>
      <span>Dale@prairielanternpopcorn.com</span>
    </li>
    <li>
      <svg viewBox="0 0 12 12" aria-hidden="true"><circle cx="6" cy="6" r="5" fill="#d7232a"/><path d="M1 6h10M6 1v10M2.5 3.5h7M2.5 8.5h7" stroke="#f7f7f7" stroke-width="0.7" fill="none"/><ellipse cx="6" cy="6" rx="2.2" ry="5" fill="none" stroke="#f7f7f7" stroke-width="0.7"/></svg>
      <span>www.prairielanternpopcorn.com</span>
    </li>
  </ul>

  <p class="tagline">"<span class="tagline__pop">POP</span>ular for a reason"</p>
</section>

</body>
</html>
```